Pine Hollow Haven Home Inc. Website Update

We have a couple of broken links such as the "contact us" and would like to add board members and a calendar of events. We are open to a new design.

```html
<!DOCTYPE html>
<html lang="en">
<head>
<meta charset="utf-8">
<title>Pine Hollow Haven Home</title>
<link rel="stylesheet" href="https://fonts.googleapis.com/css2?family=Source+Sans+3:wght@400;600;700&family=Poppins:wght@400;500;600&family=Open+Sans:ital,wght@0,400;0,600;1,400&display=swap">
<style>
:root{
  --pink:#df6a8b;
  --pink-dark:#c9557a;
  --blue:#1d78c1;
  --blue-dark:#0f5c9c;
  --ink:#1b1b1b;
  --text:#333;
  --muted:#666;
  --white:#fff;
  --cream:#f3e4c4;
  --dark:#111;
  --gold:#f08a24;
}
*{box-sizing:border-box;margin:0;padding:0}
html,body{width:1200px;height:5279px;overflow:hidden}
body{font-family:"Open Sans",sans-serif;color:var(--text);background:var(--white);position:relative}
section,header,footer{position:absolute;left:0;width:1200px}
.abs{position:absolute}
h2{font-family:"Source Sans 3",sans-serif;font-weight:600;font-size:38px;color:var(--ink);text-align:center}

/* header */
.site-header{top:0;height:140px;background:var(--white)}
.brand{left:95px;top:18px;display:flex;align-items:center;gap:10px}
.brand-dot{width:40px;height:40px;border-radius:50%;background:var(--pink)}
.brand-name{font-family:"Poppins",sans-serif;font-size:13px;font-weight:600;color:var(--pink-dark);width:120px;line-height:1.2}
.topbar{right:60px;top:0;display:flex;height:40px}
.topbar .phone{background:var(--pink);color:#fff;font-family:"Poppins",sans-serif;font-size:17px;padding:0 22px 0 30px;display:flex;align-items:center;gap:8px;clip-path:polygon(14px 0,100% 0,100% 100%,0 100%)}
.topbar .donate{background:var(--blue);color:#fff;font-family:"Poppins",sans-serif;font-weight:600;font-size:17px;padding:0 30px;display:flex;align-items:center}
.nav{right:60px;top:78px;display:flex;gap:22px;font-family:"Poppins",sans-serif;font-size:15px;color:var(--ink)}
.nav .active{color:var(--blue)}

/* hero */
.hero{top:140px;height:700px;background:linear-gradient(100deg,#fbf4e6 0%,#f4e2bd 55%,#eed6a9 100%)}
.hero-photo{left:610px;top:0;width:520px;height:560px;background:linear-gradient(180deg,#f1dcae,#e7c995 70%,#d8b27a);border-radius:0}
.hero h1{left:88px;top:125px;font-family:"Source Sans 3",sans-serif;font-weight:700;font-size:68px;line-height:0.98;color:var(--ink)}
.hero p{left:88px;top:272px;width:400px;font-size:16px;line-height:1.55;color:var(--ink)}
.btn-outline{left:88px;top:402px;width:186px;height:56px;border:2px solid var(--ink);border-radius:28px;display:flex;align-items:center;justify-content:center;font-family:"Poppins",sans-serif;font-weight:500;font-size:18px;color:var(--ink)}
.hero-wave{left:0;bottom:0;width:1200px;height:170px}

/* about */
.about{top:840px;height:620px}
.about-photo{left:88px;top:68px;width:458px;height:458px;border-radius:50%;border:10px solid var(--pink);background:linear-gradient(160deg,#dfe6ee,#9fa7b0 55%,#5d6b5a)}
.about h2{left:668px;top:75px;text-align:left;font-size:40px}
.about p{left:668px;top:144px;width:448px;font-size:13.5px;line-height:1.75;color:#444}
.btn-blue{background:var(--blue);color:#fff;border-radius:26px;display:flex;align-items:center;justify-content:center;font-family:"Poppins",sans-serif;font-weight:500}
.about .btn-blue{left:668px;top:392px;width:178px;height:52px;font-size:18px}

/* mission band */
.mission{top:1460px;height:581px;background:var(--pink)}
.mission h2{top:72px;width:100%;color:#fff;font-size:40px;font-weight:400}
.mission .lead{top:140px;width:100%;text-align:center;color:#fff;font-size:19px;line-height:1.6}
.offer{top:255px;width:220px;text-align:center}
.offer-icon{width:166px;height:166px;margin:0 auto;border-radius:50%;background:#fff;border:10px solid var(--blue-dark);display:flex;align-items:center;justify-content:center}
.offer-label{margin-top:20px;color:#fff;font-family:"Source Sans 3",sans-serif;font-weight:600;font-size:20px;line-height:1.3}

/* services */
.services{top:2041px;height:600px;background:#f7f7f7}
.services h2{top:70px;width:100%;font-size:42px;font-weight:400}
.svc{top:190px;width:260px;text-align:center}
.svc-photo{position:relative;width:232px;height:232px;margin:0 auto;border-radius:50%;border:8px solid var(--pink)}
.svc-num{position:absolute;right:-10px;bottom:22px;width:62px;height:62px;border-radius:50%;background:var(--pink);border:5px solid #fff;color:#fff;font-family:"Poppins",sans-serif;font-size:24px;font-weight:600;display:flex;align-items:center;justify-content:center}
.svc-label{margin-top:22px;font-family:"Source Sans 3",sans-serif;font-size:21px;color:var(--ink);line-height:1.3}
.arrow{top:280px;width:34px;height:34px;border-radius:50%;background:var(--blue);display:flex;align-items:center;justify-content:center}

/* events */
.events{top:2641px;height:860px;background:linear-gradient(180deg,#2b2b2b,#1a1a1a 60%,#222)}
.events h2{top:95px;width:100%;color:#fff;font-size:42px;font-weight:400}
.calendar{left:88px;top:220px;width:504px;background:#fff}
.cal-head{height:58px;display:flex;align-items:center;justify-content:space-between;padding:0 28px;font-family:"Poppins",sans-serif;font-size:24px;color:var(--ink)}
.cal-arrow{width:30px;height:30px;border-radius:50%;background:var(--blue);display:flex;align-items:center;justify-content:center}
.cal-days,.cal-grid{display:grid;grid-template-columns:repeat(7,1fr)}
.cal-days{background:#e9e9e9;height:40px;align-items:center;text-align:center;font-family:"Poppins",sans-serif;font-size:13px;color:#555}
.cal-grid div{height:70px;display:flex;align-items:center;justify-content:center;font-family:"Poppins",sans-serif;font-size:21px;background:var(--pink);color:var(--ink);border:1px solid #fff}
.cal-grid .on{background:var(--blue);color:#fff}
.cal-grid .off{background:#fff}
.event-card{left:605px;top:255px;width:508px;height:296px;background:#fff;display:flex}
.event-info{width:300px;padding:40px 22px}
.event-info h3{font-family:"Poppins",sans-serif;font-size:19px;font-weight:600;color:var(--ink);margin-bottom:12px}
.event-info p{font-size:13px;line-height:1.6;color:#444}
.event-btns{display:flex;gap:12px;margin-top:18px}
.event-btns span{height:28px;padding:0 20px;font-size:12px}
.event-photo{position:relative;flex:1;background:linear-gradient(160deg,#c9cfd6,#8f98a2 60%,#6d7682)}
.event-date{position:absolute;left:-20px;top:12px;width:54px;height:54px;border-radius:50%;background:var(--pink);color:#fff;font-size:11px;font-weight:600;display:flex;align-items:center;justify-content:center;text-align:center;line-height:1.1}
.events .view{left:626px;top:590px;width:188px;height:44px;font-size:18px}

/* team */
.team{top:3501px;height:511px;background:var(--pink)}
.team h2{top:78px;width:100%;color:#fff;font-size:40px;font-weight:400}
.member{top:190px;width:240px;text-align:center}
.member-photo{width:144px;height:144px;margin:0 auto;border-radius:50%;border:6px solid #fff;background:linear-gradient(180deg,#e9d6c8,#b99a86)}
.member-social{margin:-14px auto 0;width:128px;height:38px;border-radius:19px;background:var(--blue);display:flex;align-items:center;justify-content:center;gap:10px;position:relative}
.member-social i{width:12px;height:12px;background:#fff;border-radius:2px;display:block}
.member-name{margin-top:14px;color:#fff;font-family:"Poppins",sans-serif;font-size:16px}

/* reviews */
.reviews{top:4012px;height:720px;background:linear-gradient(180deg,#f6f1ee,#efe6e2 60%,#e8dcd8)}
.reviews h2{top:110px;width:100%;font-size:40px;font-weight:400}
.review{top:262px;width:500px;height:220px}
.review-photo{left:0;top:0;width:138px;height:138px;border-radius:50%;border:6px solid #fff;background:linear-gradient(180deg,#e6cfc0,#b9907a)}
.quote{left:40px;top:150px;font-family:"Source Sans 3",sans-serif;font-size:80px;font-weight:700;color:var(--gold);line-height:1}
.review p{left:158px;top:0;width:330px;font-size:14px;font-style:italic;line-height:1.6;color:#555}
.stars{left:158px;top:118px;display:flex;gap:4px}
.reviewer{left:178px;top:165px;font-family:"Poppins",sans-serif;font-style:italic;font-size:19px;color:var(--ink)}
.reviews-wave{left:0;bottom:0;width:1200px;height:150px}

/* footer */
.site-footer{top:4732px;height:547px;background:var(--dark);color:#fff}
.site-footer h4{font-family:"Poppins",sans-serif;font-weight:500;font-size:21px;margin-bottom:26px}
.col-form{left:98px;top:80px;width:320px}
.field{height:26px;border:1px solid #ccc;background:#fff;margin-bottom:15px;font-size:10px;color:#777;padding:5px 8px}
.field.msg{height:64px}
.submit{width:138px;height:32px;font-size:14px;border-radius:3px}
.col-contact{left:549px;top:80px;width:320px}
.contact-row{display:flex;gap:22px;align-items:flex-start;margin-bottom:26px;font-size:14px;line-height:1.5}
.ci{width:30px;height:30px;border-radius:50%;border:2px solid #fff;flex:none;display:flex;align-items:center;justify-content:center}
.col-links{left:975px;top:80px;width:200px}
.col-links li{list-style:none;font-family:"Poppins",sans-serif;font-size:14.5px;font-weight:500;line-height:1.85}
.copyright{left:0;top:480px;width:100%;text-align:center;font-size:14px;color:#ddd}
.footer-social{right:90px;top:463px;display:flex;gap:10px}
.footer-social i{width:26px;height:26px;background:#fff;border-radius:3px;display:block}
</style>
</head>
<body>

<header class="site-header">
  <div class="abs brand"><span class="brand-dot"></span><span class="brand-name">Pine Hollow Haven Home Inc.</span></div>
  <div class="abs topbar">
    <span class="phone"><svg width="16" height="16" viewBox="0 0 24 24"><path fill="#fff" d="M6.6 10.8a15 15 0 006.6 6.6l2.2-2.2c.3-.3.7-.4 1-.2 1.1.4 2.3.6 3.6.6.6 0 1 .4 1 1V20c0 .6-.4 1-1 1A17 17 0 013 4c0-.6.4-1 1-1h3.5c.6 0 1 .4 1 1 0 1.3.2 2.5.6 3.6.1.3 0 .7-.2 1z"/></svg>555.010.2747</span>
    <span class="donate">DONATE NOW</span>
  </div>
  <nav class="abs nav"><span class="active">Home</span><span>About</span><span>How You Can Help</span><span>Services Offered</span><span>Our Love of Pets</span><span>Contact Us</span><span>Angel Walk</span></nav>
</header>

<section class="hero">
  <div class="abs hero-photo" role="img" aria-label="Photo of a young woman sitting on the floor reading a book"></div>
  <h1 class="abs">Welcome to<br>North Georgia</h1>
  <p class="abs">Lorem Ipsum is simply dummy text of the printing and typesetting industry. Lorem Ipsum has been the industry's standard dummy text ever since the 1500s</p>
  <span class="abs btn-outline">Read More</span>
  <svg class="abs hero-wave" viewBox="0 0 1200 170" preserveAspectRatio="none">
    <path d="M0 60 C300 150 700 170 1200 20 L1200 170 L0 170Z" fill="#fff"/>
    <path d="M0 55 C300 140 700 160 1200 10 L1200 40 C700 185 300 165 0 90Z" fill="var(--blue)"/>
    <path d="M0 100 C300 170 700 180 1200 55 L1200 75 C700 195 300 190 0 120Z" fill="var(--blue-dark)"/>
  </svg>
</section>

<section class="about">
  <div class="abs about-photo" role="img" aria-label="Photo of the two-storey house with a front porch and a flowering tree"></div>
  <h2 class="abs">About Us</h2>
  <p class="abs">Pine Hollow Haven Home is home to 10 girls ranging in ages from 12-21. The home has seven bedrooms and four bathrooms with a large spa tub for relaxing. Our kitchen takes on the aroma of a restaurant in the evenings as the girls practice their Independent Living Skills with menu planning and preparation in a supervised setting. When the girls are not cooking or relaxing in their rooms, they may be found in the family room where community meetings are held to problem solve.</p>
  <span class="abs btn-blue">Read More</span>
</section>

<section class="mission">
  <h2 class="abs">We are Pine Hollow Haven Home</h2>
  <p class="abs lead">With the help of our community, we have raised over 1000 girls and counting! Some of<br>the services we offer include:</p>
  <div class="abs offer" style="left:133px">
    <div class="offer-icon"><svg width="60" height="70" viewBox="0 0 60 70" fill="none" stroke="#222" stroke-width="3"><rect x="14" y="4" width="32" height="62" rx="3"/><line x1="22" y1="18" x2="38" y2="18"/><line x1="22" y1="30" x2="38" y2="30"/><line x1="22" y1="42" x2="38" y2="42"/></svg></div>
    <div class="offer-label">Room, Board, and<br>Watchful Oversight</div>
  </div>
  <div class="abs offer" style="left:369px">
    <div class="offer-icon"><svg width="70" height="64" viewBox="0 0 70 64"><path d="M35 58 L8 31 A15 15 0 0135 10 A15 15 0 0162 31Z" fill="none" stroke="#222" stroke-width="3.5"/></svg></div>
    <div class="offer-label">Transitional Living<br>Services</div>
  </div>
  <div class="abs offer" style="left:618px">
    <div class="offer-icon"><svg width="64" height="68" viewBox="0 0 64 68" fill="none" stroke="#222" stroke-width="3"><path d="M16 62 V46 A24 24 0 1152 40 L56 48 H48 V58 H34 V62"/><circle cx="34" cy="26" r="8"/></svg></div>
    <div class="offer-label">Independent Living<br>Services</div>
  </div>
  <div class="abs offer" style="left:854px">
    <div class="offer-icon"><svg width="72" height="56" viewBox="0 0 72 56" fill="none" stroke="#222" stroke-width="3"><path d="M4 20 L18 8 L34 14 L54 8 L68 20 L50 40 L40 48 L24 34"/><path d="M34 14 L24 26 L30 30 L40 22"/></svg></div>
    <div class="offer-label">Foster Gift Shop</div>
  </div>
</section>

<section class="services">
  <h2 class="abs">Our Services</h2>
  <span class="abs arrow" style="left:25px"><svg width="12" height="12" viewBox="0 0 12 12"><path d="M8 1 L3 6 L8 11" stroke="#fff" stroke-width="2" fill="none"/></svg></span>
  <span class="abs arrow" style="left:1140px"><svg width="12" height="12" viewBox="0 0 12 12"><path d="M4 1 L9 6 L4 11" stroke="#fff" stroke-width="2" fill="none"/></svg></span>
  <div class="abs svc" style="left:70px"><div class="svc-photo" role="img" aria-label="Photo of a girl relaxing with a mug at home" style="background:linear-gradient(160deg,#f3d7cc,#c98d7e)"><span class="svc-num">1</span></div><div class="svc-label">Independent Living<br>Housing</div></div>
  <div class="abs svc" style="left:327px"><div class="svc-photo" role="img" aria-label="Photo of a girl cooking in a kitchen" style="background:linear-gradient(160deg,#6b3a32,#2a1c1a)"><span class="svc-num">2</span></div><div class="svc-label">Life Skills Classes</div></div>
  <div class="abs svc" style="left:591px"><div class="svc-photo" role="img" aria-label="Photo of a teenage girl holding a clock" style="background:linear-gradient(160deg,#f6f1e8,#d6c7a8)"><span class="svc-num">3</span></div><div class="svc-label">Teen Time</div></div>
  <div class="abs svc" style="left:855px"><div class="svc-photo" role="img" aria-label="Photo of a group of smiling friends" style="background:linear-gradient(160deg,#d9c3b0,#8c6a55)"><span class="svc-num">4</span></div><div class="svc-label">Behavior Modification</div></div>
</section>

<section class="events">
  <h2 class="abs">Upcoming Events</h2>
  <div class="abs calendar">
    <div class="cal-head"><span class="cal-arrow"><svg width="10" height="10" viewBox="0 0 10 10"><path d="M7 1 L3 5 L7 9" stroke="#fff" stroke-width="2" fill="none"/></svg></span>Oct 2019<span class="cal-arrow"><svg width="10" height="10" viewBox="0 0 10 10"><path d="M3 1 L7 5 L3 9" stroke="#fff" stroke-width="2" fill="none"/></svg></span></div>
    <div class="cal-days"><span>MON</span><span>TUE</span><span>WED</span><span>THU</span><span>FRI</span><span>SAT</span><span>SUN</span></div>
    <div class="cal-grid">
      <div class="off">28</div><div>1</div><div>2</div><div>3</div><div class="on">4</div><div>5</div><div>6</div>
      <div>7</div><div>8</div><div>9</div><div class="on">10</div><div>11</div><div class="on">12</div><div>13</div>
      <div>14</div><div>15</div><div>16</div><div>17</div><div>18</div><div class="on">19</div><div>20</div>
      <div>21</div><div class="on">22</div><div>23</div><div>24</div><div>25</div><div>26</div><div>27</div>
      <div>28</div><div>29</div><div>30</div><div>31</div><div class="off">1</div><div class="off">2</div><div class="off">3</div>
    </div>
  </div>
  <div class="abs event-card">
    <div class="event-info">
      <h3>Lorem Impsum dolar sit</h3>
      <p>Lorem Ipsum is simply dummy text of the printing and typesetting industry. Lorem Ipsum has been the industry's standard dummy text ever since the 1500s Industry</p>
      <div class="event-btns"><span class="btn-blue">Read More</span><span class="btn-blue">Book Now</span></div>
    </div>
    <div class="event-photo" role="img" aria-label="Photo of a group of girls sitting together"><span class="event-date">Oct<br>2019</span></div>
  </div>
  <span class="abs btn-blue view">View More</span>
</section>

<section class="team">
  <h2 class="abs">Our Team</h2>
  <div class="abs member" style="left:91px"><div class="member-photo" role="img" aria-label="Portrait photo of a team member"></div><div class="member-social"><i></i><i></i><i></i><i></i></div><div class="member-name">Dr. Meera Kallan</div></div>
  <div class="abs member" style="left:355px"><div class="member-photo" role="img" aria-label="Portrait photo of a team member"></div><div class="member-social"><i></i><i></i><i></i><i></i></div><div class="member-name">Rohan Desilva</div></div>
  <div class="abs member" style="left:619px"><div class="member-photo" role="img" aria-label="Portrait photo of a team member"></div><div class="member-social"><i></i><i></i><i></i><i></i></div><div class="member-name">Lina Farrow</div></div>
  <div class="abs member" style="left:883px"><div class="member-photo" role="img" aria-label="Portrait photo of a team member"></div><div class="member-social"><i></i><i></i><i></i><i></i></div><div class="member-name">Marco Estevan</div></div>
</section>

<section class="reviews" role="img" aria-label="Faded background photo of girls laughing together on a sofa">
  <h2 class="abs">Customers Reviews</h2>
  <div class="abs review" style="left:95px">
    <div class="abs review-photo" role="img" aria-label="Portrait photo of a reviewer"></div>
    <span class="abs quote">&ldquo;&ldquo;</span>
    <p class="abs">Lorem Ipsum is simply dummy text of the printing and typesetting industry. Lorem Ipsum has been the industry's standard dummy text ever since the 1500s</p>
    <div class="abs stars"><svg width="150" height="24" viewBox="0 0 150 24"><g fill="var(--gold)"><path id="st" d="M12 1 L15 9 L23 9 L17 14 L19 22 L12 17 L5 22 L7 14 L1 9 L9 9Z"/><use href="#st" x="30"/><use href="#st" x="60"/><use href="#st" x="90"/><use href="#st" x="120"/></g></svg></div>
    <span class="abs reviewer">John Doe</span>
  </div>
  <div class="abs review" style="left:615px">
    <div class="abs review-photo" role="img" aria-label="Portrait photo of a reviewer"></div>
    <span class="abs quote">&ldquo;&ldquo;</span>
    <p class="abs">Lorem Ipsum is simply dummy text of the printing and typesetting industry. Lorem Ipsum has been the industry's standard dummy text ever since the 1500s</p>
    <div class="abs stars"><svg width="150" height="24" viewBox="0 0 150 24"><g fill="var(--gold)"><use href="#st"/><use href="#st" x="30"/><use href="#st" x="60"/><use href="#st" x="90"/><use href="#st" x="120"/></g></svg></div>
    <span class="abs reviewer">John Doe</span>
  </div>
  <svg class="abs reviews-wave" viewBox="0 0 1200 150" preserveAspectRatio="none">
    <path d="M0 40 C400 150 800 150 1200 30 L1200 150 L0 150Z" fill="var(--dark)"/>
    <path d="M0 20 C400 130 800 130 1200 10 L1200 35 C800 160 400 160 0 50Z" fill="var(--blue)"/>
    <path d="M0 60 C400 165 800 165 1200 50 L1200 65 C800 180 400 180 0 78Z" fill="#fff"/>
  </svg>
</section>

<footer class="site-footer">
  <div class="abs col-form">
    <h4>Get In Touch</h4>
    <div class="field">First Name</div>
    <div class="field">Email Address</div>
    <div class="field">Phone Number</div>
    <div class="field msg">Message</div>
    <span class="btn-blue submit">Submit</span>
  </div>
  <div class="abs col-contact">
    <h4>Contact Us</h4>
    <div class="contact-row"><span class="ci"><svg width="12" height="16" viewBox="0 0 12 16"><path d="M6 0A6 6 0 000 6c0 4 6 10 6 10s6-6 6-10A6 6 0 006 0zm0 8a2 2 0 110-4 2 2 0 010 4z" fill="#fff"/></svg></span><span>418 Cedar Ridge Rd,<br>Lakeview, GA 30000,<br>USA</span></div>
    <div class="contact-row"><span class="ci"><svg width="14" height="14" viewBox="0 0 24 24"><path fill="#fff" d="M6.6 10.8a15 15 0 006.6 6.6l2.2-2.2c.3-.3.7-.4 1-.2 1.1.4 2.3.6 3.6.6.6 0 1 .4 1 1V20c0 .6-.4 1-1 1A17 17 0 013 4c0-.6.4-1 1-1h3.5c.6 0 1 .4 1 1 0 1.3.2 2.5.6 3.6.1.3 0 .7-.2 1z"/></svg></span><span>Call Us :<br>555.010.2747</span></div>
    <div class="contact-row"><span class="ci"><svg width="14" height="11" viewBox="0 0 14 11"><rect x="0.5" y="0.5" width="13" height="10" fill="none" stroke="#fff"/><path d="M0.5 0.5 L7 6 L13.5 0.5" fill="none" stroke="#fff"/></svg></span><span style="padding-top:5px">info@pinehollowhaven.org</span></div>
  </div>
  <div class="abs col-links">
    <h4>Quick Links</h4>
    <ul><li>Home</li><li>About</li><li>How You Can Help</li><li>Services Offered</li><li>Our Love of Pets</li><li>Contact Us</li><li>Angel Walk</li></ul>
  </div>
  <div class="abs copyright">&copy; 2019Copyrights | All Rights Reserved</div>
  <div class="abs footer-social"><i></i><i></i><i></i><i></i></div>
</footer>

</body>
</html>
```